Business Card Re-Design/Update

We'd like to update out business cards. I've included our current "Style guide" which has the colour scheme of the organisation in it. I've also included the branding files with logos etc in them.

I've also included a copy of one of our existing cards so that you can see how ugly/dated they look. I'd like a fresh modern corporate look.

Target Market(s)

These are for our clients, potential clients, industry contacts - like all business cards

Contact Information for Business Card

Name
Position
Company Address - Level 1, 47 Fernby Street, Carlow Qld 4072
Direct Phone
mobile
Email
Website -www.korvalit.com.au
Logo

Colors

Designer to choose colors to be used in the design.

Requirements
Must have
• Main Logo
• Cards will need to be editable to be able to personalize them for each new employee.
Nice to have
• The MapOut, ShipWell, KeepSteady would be okay to have if they can be sensibly and professionally added to the look without detracting from the main imagery.
• Maybe they could go on the back of the card? will leave this to your creative discretion as to whether/where they fit.
Should not have
• Should not have decorative or script fonts

```html
<!DOCTYPE html>
<html lang="en">
<head>
<meta charset="utf-8">
<title>Korvalit Business Card</title>
<link rel="stylesheet" href="https://fonts.googleapis.com/css2?family=Work+Sans:wght@400;500;600&display=swap">
<style>
  :root {
    --stage: #2b2b2b;
    --card-dark: #3a3a3c;
    --card-light: #ffffff;
    --light-shade: #e6e6e6;
    --brand-red: #d0161c;
    --text-light: #f2f2f2;
    --text-grey: #c9c9c9;
    --text-dark: #3a3a3c;
  }
  * { box-sizing: border-box; margin: 0; padding: 0; }
  html, body { width: 1200px; height: 900px; overflow: hidden; }
  body {
    background: var(--stage);
    font-family: "Work Sans", Arial, sans-serif;
    display: flex;
    flex-direction: column;
    align-items: center;
    justify-content: center;
    gap: 56px;
  }
  .card {
    position: relative;
    width: 630px;
    height: 360px;
    overflow: hidden;
    box-shadow: 0 14px 34px rgba(0,0,0,0.45);
  }
  .card-front { background: linear-gradient(135deg, var(--light-shade), var(--card-light) 45%); }
  .front-panel { position: absolute; inset: 0; width: 100%; height: 100%; }
  .front-panel polygon { fill: var(--card-dark); }

  .brand {
    position: absolute;
    display: flex;
    align-items: center;
    gap: 12px;
  }
  .brand-square { background: var(--brand-red); }
  .brand-name { font-weight: 500; letter-spacing: -0.5px; }

  .card-front .brand { left: 42px; top: 150px; }
  .card-front .brand-square { width: 26px; height: 26px; }
  .card-front .brand-name { font-size: 40px; color: var(--text-dark); }

  .contact {
    position: absolute;
    left: 340px;
    top: 70px;
    color: var(--text-light);
    font-size: 13px;
    line-height: 1.55;
  }
  .contact-name {
    color: var(--brand-red);
    font-size: 26px;
    font-weight: 500;
    text-transform: uppercase;
    letter-spacing: 0.5px;
    line-height: 1.1;
  }
  .contact-role { font-size: 13.5px; margin-bottom: 10px; }
  .contact-address { margin-bottom: 10px; }
  .contact-list { list-style: none; }
  .contact-list li { display: flex; align-items: center; gap: 9px; }
  .contact-list svg { width: 10px; height: 10px; flex: none; }
  .contact-list svg * { fill: var(--brand-red); }
  .web-accent { color: var(--brand-red); }

  .card-back { background: var(--card-dark); }
  .card-back .brand { left: 50%; top: 50%; transform: translate(-50%, -50%); gap: 18px; }
  .card-back .brand-square { width: 44px; height: 44px; }
  .card-back .brand-name { font-size: 66px; color: var(--text-grey); }
</style>
</head>
<body>
  <section class="card card-front" aria-label="Business card front">
    <svg class="front-panel" viewBox="0 0 630 360" preserveAspectRatio="none" aria-hidden="true">
      <polygon points="318,0 630,0 630,360 318,360 318,96 306,88 318,80"/>
    </svg>
    <div class="brand">
      <span class="brand-square"></span>
      <span class="brand-name">korvalit</span>
    </div>
    <div class="contact">
      <p class="contact-name">Maren Holt</p>
      <p class="contact-role">Business Development Manager</p>
      <p class="contact-address">Unit 12/8 Tarrow Lane,<br>Carlow QLD 4072</p>
      <ul class="contact-list">
        <li><svg viewBox="0 0 10 10"><rect x="2" y="0" width="6" height="10" rx="1"/></svg>+61 (0)400 555 018</li>
        <li><svg viewBox="0 0 10 10"><path d="M0 4 Q5 0 10 4 L8 5 L7 3 L3 3 L2 5 Z M2 6 H8 V10 H2 Z"/></svg>+61 (0)7 5550 1216</li>
        <li><svg viewBox="0 0 10 10"><path d="M1 1 L4 1 L5 3 L3.5 4.5 Q5 6.5 5.5 6.5 L7 5 L9 6 L9 9 Q3 9 1 1 Z"/></svg>+61 (0)7 5550 1233</li>
        <li><svg viewBox="0 0 10 10"><rect x="1" y="3" width="8" height="5"/><rect x="3" y="0" width="4" height="3"/></svg>+61 (0)7 5550 1203</li>
        <li><svg viewBox="0 0 10 10"><path d="M0 2 H10 V8 H0 Z M0 2 L5 6 L10 2" /></svg>mholt@korvalit.com.au</li>
        <li><svg viewBox="0 0 10 10"><circle cx="5" cy="5" r="5"/></svg>www.<span class="web-accent">korvalit</span>.com.au</li>
      </ul>
    </div>
  </section>

  <section class="card card-back" aria-label="Business card back">
    <div class="brand">
      <span class="brand-square"></span>
      <span class="brand-name">korvalit</span>
    </div>
  </section>
</body>
</html>
```